Redesign of business card for Cedar Ridge Mechanical

We are looking for a new design for our business cards for Cedar Ridge Mechanical. We are a plumbing & HVAC construction company, operating on the West Coast of Canada and USA. Logo attached.
Industry/Entity Type
Construction - Plumbing & HVAC
Contact Information for Business Card
Name, address, phone numbers, email, website address
Look and feel
Each slider illustrates characteristics of the customer's brand and the style your logo design should communicate.

```html
<!DOCTYPE html>
<html lang="en">
<head>
<meta charset="UTF-8">
<title>Cedar Ridge Mechanical – Business Card</title>
<link href="https://fonts.googleapis.com/css2?family=Montserrat:wght@400;700&display=swap" rel="stylesheet">
<style>
  :root {
    --ink: #0a0a0a;
    --paper: #ffffff;
    --backdrop: #2b2b2b;
    --muted: #3a3a3a;
  }
  * { box-sizing: border-box; margin: 0; padding: 0; }
  html, body { width: 1200px; height: 880px; overflow: hidden; }
  body {
    background: var(--backdrop);
    font-family: "Montserrat", sans-serif;
    position: relative;
  }
  .card {
    position: absolute;
    width: 640px;
    height: 366px;
    border-radius: 28px;
    overflow: hidden;
  }
  .card--front {
    left: 80px; top: 60px;
    background: var(--ink);
    display: flex; align-items: center; justify-content: center;
  }
  .card--back {
    left: 480px; top: 460px;
    background: var(--paper);
    color: var(--ink);
  }
  .brand {
    display: flex; align-items: center; gap: 16px;
    font-weight: 700; letter-spacing: 0.04em; text-transform: uppercase;
  }
  .brand__mark { flex: none; }
  .card--front .brand { color: var(--paper); font-size: 30px; }
  .card--front .brand__mark { width: 44px; height: 44px; background: var(--paper); }
  .card--back .brand {
    position: absolute; left: 40px; top: 46px;
    font-size: 20px;
  }
  .card--back .brand__mark { width: 30px; height: 30px; background: var(--ink); }
  .holder {
    position: absolute; right: 34px; top: 38px;
    text-align: right;
    padding-right: 4px;
  }
  .holder__name { font-size: 24px; font-weight: 700; letter-spacing: 0.02em; }
  .holder__title { font-size: 14px; font-weight: 400; color: var(--muted); margin-top: 2px; }
  .edge-bar {
    position: absolute; right: 0; top: 34px;
    width: 14px; height: 40px; background: var(--ink);
  }
  .address {
    position: absolute; right: 34px; top: 178px;
    text-align: right; font-size: 15px; line-height: 1.5; color: var(--muted);
  }
  .contacts {
    position: absolute; left: 40px; bottom: 30px;
    list-style: none; font-size: 16px; line-height: 1;
  }
  .contacts li { display: flex; align-items: center; gap: 10px; margin-top: 10px; }
  .contacts svg { width: 16px; height: 16px; fill: var(--ink); flex: none; }
</style>
</head>
<body>
  <section class="card card--front" aria-label="Card front">
    <div class="brand">
      <span class="brand__mark"></span>
      <span class="brand__name">Cedar Ridge Mechanical</span>
    </div>
  </section>

  <section class="card card--back" aria-label="Card back">
    <div class="brand">
      <span class="brand__mark"></span>
      <span class="brand__name">Cedar Ridge Mechanical</span>
    </div>

    <div class="edge-bar"></div>
    <div class="holder">
      <p class="holder__name">DANIEL HAYES</p>
      <p class="holder__title">Managing Director</p>
    </div>

    <p class="address">Your address, City<br>State, Zip 1234</p>

    <ul class="contacts">
      <li>
        <svg viewBox="0 0 16 16" aria-hidden="true"><path d="M2 5c0-2 2-3 6-3s6 1 6 3v1h-3V5H5v1H2zM4 7h8l2 7H2z"/></svg>
        <span>123 456 789</span>
      </li>
      <li>
        <svg viewBox="0 0 16 16" aria-hidden="true"><path d="M1 3h14v10H1zm1.5 1.5v.4L8 9l5.5-4.1v-.4z"/></svg>
        <span>info@yourmail.com</span>
      </li>
      <li>
        <svg viewBox="0 0 16 16" aria-hidden="true"><circle cx="8" cy="8" r="7"/></svg>
        <span>www.yourwebsite.com</span>
      </li>
    </ul>
  </section>
</body>
</html>
```